ULMIRA card Technical Architecture

Hello everyone ULMIRA: It is a consulting firm in Architecture and Construction. I require a card duplexing, sober, elegant, classic but not boring. Update 1: Use the following data for the card. Name: Gonzalo Pereda Mauricio Villalta Position: COO Twitter: @ulmiraAT Homepage: ulmira-example.com home address not include the participation of all thank you.

Target Market(s)

Construction companies, Architects and Consulting Engineers

Industry/Entity Type

Consulting

Contact Information for Business Card

Los campos que debe tener:
Nombre, Cargo, email, homepage y twitter

Font styles to use
Serif
Sans Serif
Other font styles liked:
• Me gustan playfair display, open sans y roboto, pero estoy sujeto a sus propuestas

Requirements
Must have
• Colors: Present combined proposals in white, red, gray and black Update 1: The two names must be clearly differentiated from the two surnames
Nice to have
• They are free to present their best proposals. I will bring them immediate feedback to the extent you can go see their designs. Complete data for card and logo files will give the winner the

```html
<!DOCTYPE html>
<html lang="es">
<head>
<meta charset="utf-8">
<title>ULMIRA – Tarjeta de presentación</title>
<link rel="stylesheet" href="https://fonts.googleapis.com/css2?family=Open+Sans:wght@300;400;600;700&display=swap">
<style>
  :root{
    --stage:#2b2b2d;
    --red-light:#c1262f;
    --red-mid:#9c1720;
    --red-dark:#5a0a10;
    --wine:#7a0f17;
    --ink:#2a2a2a;
    --rule:#3a3a3a;
    --white:#ffffff;
  }
  *{box-sizing:border-box;margin:0;padding:0}
  html,body{width:1200px;height:900px;overflow:hidden;background:var(--stage);font-family:"Open Sans",Arial,sans-serif}
  .canvas{position:relative;width:1200px;height:900px}
  .card{position:absolute;left:250px;width:700px;height:400px;border-radius:22px;overflow:hidden}

  .card-front{top:30px;background:radial-gradient(ellipse at 45% 35%,var(--red-light) 0%,var(--red-mid) 45%,var(--red-dark) 100%);color:var(--white)}
  .front-brand{position:absolute;left:120px;top:140px;width:360px;text-align:center}
  .brand-name{font-weight:300;font-size:58px;letter-spacing:20px;padding-left:20px;line-height:1}
  .brand-rule{height:1px;background:var(--white);opacity:.8;margin:16px 0 10px}
  .brand-tagline{font-weight:400;font-size:16px;letter-spacing:6px}
  .social{position:absolute;right:44px;top:200px;display:flex;align-items:center;gap:8px;font-size:15px;font-weight:400}
  .social-dot{width:12px;height:12px;border-radius:50%;background:var(--white)}

  .card-back{top:470px;background:var(--white)}
  .back-band{position:absolute;left:0;bottom:0;width:700px;height:400px}
  .back-brand{position:absolute;left:40px;top:160px;width:240px;display:flex;align-items:center;gap:12px;color:var(--wine)}
  .back-brand-square{width:18px;height:18px;background:var(--wine)}
  .back-brand-name{font-weight:700;font-size:40px;letter-spacing:4px;line-height:1}
  .divider{position:absolute;left:318px;top:70px;width:1px;height:200px;background:linear-gradient(var(--white),var(--rule) 30%,var(--rule) 70%,var(--white))}
  .contact{position:absolute;left:352px;top:72px;color:var(--ink)}
  .given-names,.surnames{font-weight:700;font-size:27px;color:var(--wine);line-height:1.1}
  .role{font-size:15px;font-weight:400;margin:2px 0 10px 4px;color:var(--ink)}
  .details{list-style:none;margin-top:6px}
  .details li{display:flex;align-items:center;gap:10px;font-size:16px;line-height:1.55;color:var(--ink)}
  .details svg{width:13px;height:13px;flex:none}
</style>
</head>
<body>
<main class="canvas">

  <section class="card card-front" aria-label="Anverso">
    <div class="front-brand">
      <div class="brand-name">ULMIRA</div>
      <div class="brand-rule"></div>
      <div class="brand-tagline">ARQUITECTURA TÉCNICA</div>
    </div>
    <div class="social"><span class="social-dot"></span><span>@ulmiraAT</span></div>
  </section>

  <section class="card card-back" aria-label="Reverso">
    <svg class="back-band" viewBox="0 0 700 400" aria-hidden="true">
      <defs>
        <linearGradient id="bandGrad" x1="0" x2="1">
          <stop offset="0" stop-color="#c1262f"/>
          <stop offset="1" stop-color="#6d0c13"/>
        </linearGradient>
      </defs>
      <polygon points="0,386 440,386 470,336 700,336 700,400 0,400" fill="url(#bandGrad)"/>
      <polygon points="440,386 470,336 476,336 446,386" fill="#ffffff"/>
    </svg>

    <div class="back-brand">
      <span class="back-brand-square"></span>
      <span class="back-brand-name">ULMIRA</span>
    </div>

    <div class="divider"></div>

    <div class="contact">
      <div class="given-names">Mauricio Gonzalo</div>
      <div class="role">COO</div>
      <div class="surnames">Pereda Villalta</div>
      <div class="role">Director de Operaciones</div>
      <ul class="details">
        <li>
          <svg viewBox="0 0 16 16"><path d="M3 1l3 3-1.5 2a9 9 0 0 0 5.5 5.5L12 10l3 3-2 2C7 15 1 9 1 3z" fill="#9c1720"/></svg>
          (+570) 555 010 2030
        </li>
        <li>
          <svg viewBox="0 0 16 16"><rect x="1" y="3" width="14" height="10" rx="1" fill="none" stroke="#9c1720" stroke-width="1.8"/><path d="M1.5 3.5L8 9l6.5-5.5" fill="none" stroke="#9c1720" stroke-width="1.8"/></svg>
          info@ulmira-example.com
        </li>
        <li>
          <svg viewBox="0 0 16 16"><circle cx="8" cy="8" r="6.5" fill="none" stroke="#9c1720" stroke-width="1.6"/><ellipse cx="8" cy="8" rx="3" ry="6.5" fill="none" stroke="#9c1720" stroke-width="1.2"/><path d="M1.5 8h13" stroke="#9c1720" stroke-width="1.2"/></svg>
          www.ulmira-example.com
        </li>
      </ul>
    </div>
  </section>

</main>
</body>
</html>
```